Copperleaf Roofing Business Card

This is my current business card. But I’d like to make some changes. Somewhere on the card I’d like to list some of the services we offer. Maybe on the back? But I’d still like to keep the red. White and black modern look.

-residential & commercial roofing
-Roof Repairs & Maintenance
-Storm Damage & Insurance Claims specialist
-Christmas Lights and permanent Christmas lights
Fencing. Windows. Gutters. Siding. Sheetrock, painting.

```html
<!DOCTYPE html>
<html lang="en">
<head>
<meta charset="utf-8">
<title>Copperleaf Roofing Co. – Business Card</title>
<link rel="stylesheet" href="https://fonts.googleapis.com/css2?family=Orbitron:wght@500;800&family=Roboto:wght@400&display=swap">
<style>
  :root {
    --page-bg: #ededed;
    --card-white: #ffffff;
    --brand-red: #e31e24;
    --deep-red: #931a1e;
    --ink: #111111;
    --text-dark: #333333;
    --text-grey: #8f8f8f;
    --rule-grey: #c4c4c4;
    --owner-grey: #555555;
  }
  * { margin: 0; padding: 0; box-sizing: border-box; }
  html, body {
    width: 1200px; height: 1000px; overflow: hidden;
    background: var(--page-bg);
  }
  .canvas { position: relative; width: 1200px; height: 1000px; }

  .card {
    position: absolute; left: 252px; width: 694px; height: 400px;
    border-radius: 26px; overflow: hidden;
  }
  .card--front { top: 72px; background: var(--card-white); }
  .card--back { top: 514px; }

  /* Front: brand block */
  .brand {
    position: absolute; left: 340px; top: 0; width: 230px;
    left: 340px;
  }
  .brand-block {
    position: absolute; left: 90px; top: 103px; width: 226px;
    text-align: center;
  }
  .brand-dot {
    width: 92px; height: 92px; border-radius: 50%;
    background: var(--brand-red); margin: 0 auto 16px;
  }
  .brand-name {
    font-family: "Orbitron", sans-serif; font-weight: 800;
    font-size: 19px; line-height: 23px; color: var(--brand-red);
    letter-spacing: 0.5px;
  }

  .divider-vertical {
    position: absolute; left: 348px; top: 94px; width: 1px; height: 166px;
    background: var(--rule-grey);
  }

  /* Front: contact block */
  .contact {
    position: absolute; left: 368px; top: 102px; width: 240px;
    text-align: center;
  }
  .person-name {
    font-family: "Orbitron", sans-serif; font-weight: 800;
    font-size: 18px; line-height: 22px; color: var(--ink); letter-spacing: 0.5px;
  }
  .person-name .surname { color: var(--brand-red); }
  .person-role {
    font-family: "Orbitron", sans-serif; font-weight: 500;
    font-size: 13px; letter-spacing: 4px; color: var(--owner-grey);
    margin-top: 1px;
  }
  .contact-icons {
    display: flex; justify-content: center; gap: 5px; margin-top: 12px;
  }
  .contact-icon {
    width: 26px; height: 26px; border-radius: 50%;
    background: var(--brand-red);
    display: flex; align-items: center; justify-content: center;
  }
  .contact-lines {
    margin-top: 9px;
    font-family: "Roboto", sans-serif; font-size: 16px; line-height: 19.5px;
    color: var(--text-dark);
  }

  .divider-horizontal {
    position: absolute; left: 69px; top: 293px; width: 555px; height: 2px;
    background: var(--rule-grey);
  }
  .services {
    position: absolute; left: 50px; top: 305px; width: 594px;
    text-align: center;
    font-family: "Roboto", sans-serif; font-size: 16px; line-height: 23px;
    color: var(--text-grey);
  }

  /* Back */
  .back-pattern {
    position: absolute; inset: 0;
    background: linear-gradient(135deg, var(--deep-red) 0%, var(--brand-red) 55%, #5a1012 100%);
  }
  .back-mark {
    position: absolute; inset: 0;
    display: flex; flex-direction: column; align-items: center; justify-content: center;
  }
  .back-mark-name {
    font-family: "Orbitron", sans-serif; font-weight: 800;
    font-size: 40px; line-height: 48px; color: var(--card-white);
    text-align: center; letter-spacing: 1px;
  }
</style>
</head>
<body>
<div class="canvas">

  <section class="card card--front">
    <div class="brand-block">
      <div class="brand-dot"></div>
      <div class="brand-name">COPPERLEAF<br>ROOFING CO.</div>
    </div>

    <div class="divider-vertical"></div>

    <div class="contact">
      <div class="person-name">DANA <span class="surname">WHITFIELD</span></div>
      <div class="person-role">OWNER</div>
      <div class="contact-icons">
        <span class="contact-icon" aria-label="Phone">
          <svg width="14" height="14" viewBox="0 0 24 24"><path fill="#fff" d="M6.6 10.8a15.1 15.1 0 0 0 6.6 6.6l2.2-2.2c.3-.3.7-.4 1-.2 1.1.4 2.3.6 3.6.6.6 0 1 .4 1 1V20c0 .6-.4 1-1 1A17 17 0 0 1 3 4c0-.6.4-1 1-1h3.5c.6 0 1 .4 1 1 0 1.3.2 2.5.6 3.6.1.3 0 .7-.2 1z"/></svg>
        </span>
        <span class="contact-icon" aria-label="Email">
          <svg width="14" height="14" viewBox="0 0 24 24"><rect x="2" y="5" width="20" height="14" rx="1.5" fill="none" stroke="#fff" stroke-width="2"/><path d="M3 6l9 7 9-7" fill="none" stroke="#fff" stroke-width="2"/></svg>
        </span>
        <span class="contact-icon" aria-label="Website">
          <svg width="14" height="14" viewBox="0 0 24 24" fill="none" stroke="#fff" stroke-width="1.8"><circle cx="12" cy="12" r="9.5"/><ellipse cx="12" cy="12" rx="4" ry="9.5"/><path d="M2.5 12h19M4 7h16M4 17h16"/></svg>
        </span>
      </div>
      <div class="contact-lines">
        682-555-0148<br>
        dana@copperleafroofing.com<br>
        copperleafroofing.com
      </div>
    </div>

    <div class="divider-horizontal"></div>

    <p class="services">
      Residential &amp; Commercial Roofing • Roof Repairs &amp; Maintenance • Storm<br>
      Damage &amp; Insurance Claims Specialist&nbsp; • Christmas Lights and Permanent<br>
      Christmas Lights • Fencing • Windows • Gutters • Siding • Sheetrock •&nbsp; Painting
    </p>
  </section>

  <section class="card card--back">
    <div class="back-pattern" role="img" aria-label="Red, dark red and black tartan block pattern with diagonal stripes"></div>
    <div class="back-mark">
      <div class="back-mark-name">COPPERLEAF<br>ROOFING CO.</div>
    </div>
  </section>

</div>
</body>
</html>
```